Best local air conditioning and heating contractor

We need a website design for a new company in Tampa Bay called the Coastal Breeze Cooling Company. We provide superior services for residential and commercial properties as well as maintenance and installing HVAC systems. We also want to sell equipment, parts and filter on the website as well. We want it easy to use for customers. Rich with content and keywords for our area.

Target Market(s)

homeowners in Tampa Bay

Industry/Entity Type

HVAC air conditioning and heating

Coding

Coded - Design and coding required

Number of Pages Required

5+ page

Font styles to use
Sans Serif

Requirements
Nice to have
• would like the colors to be same as logo

```html
<!DOCTYPE html>
<html lang="en">
<head>
<meta charset="utf-8">
<title>Coastal Breeze Cooling Company – Heating &amp; Air Conditioning, Tampa Bay</title>
<link href="https://fonts.googleapis.com/css2?family=Poppins:ital,wght@0,400;0,500;0,600;0,700;0,800;1,400&display=swap" rel="stylesheet">
<style>
:root{
  --navy:#2a3676;
  --navy-dark:#1f2a5c;
  --red:#d8222b;
  --ink:#222;
  --muted:#666;
  --light:#eef0f3;
  --white:#fff;
  --footer:#101010;
}
*{box-sizing:border-box;margin:0;padding:0}
html,body{width:1200px;height:4823px;overflow:hidden}
body{position:relative;font-family:'Poppins',sans-serif;color:var(--ink);background:var(--white)}
.abs{position:absolute}
.btn{position:absolute;display:flex;align-items:center;justify-content:center;color:var(--white);background:var(--red);font-weight:500;text-transform:uppercase;letter-spacing:.5px;z-index:2}
.btn.navy{background:var(--navy-dark)}
.ph{position:absolute}

/* header */
.topbar{left:305px;top:0;width:895px;height:37px;background:var(--red);color:var(--white);font-size:14px}
.topbar .item{position:absolute;top:9px;display:flex;align-items:center;gap:10px}
.social{position:absolute;top:10px;display:flex;gap:12px;right:50px}
.social span{width:17px;height:17px;border-radius:50%;background:var(--white)}
.brand{left:55px;top:22px;width:210px;color:var(--navy);font-weight:800;font-size:17px;line-height:1.1;text-transform:uppercase;display:flex;gap:8px;align-items:flex-start}
.brand i{display:block;width:16px;height:16px;background:var(--red);flex:none;margin-top:3px}
.nav{left:342px;top:62px;font-size:16px;font-weight:500;color:var(--ink)}
.nav a{color:inherit;text-decoration:none;position:absolute;white-space:nowrap}

/* hero */
.hero{left:0;top:105px;width:1200px;height:621px;background:var(--light)}
.hero-photo{left:505px;top:0;width:695px;height:621px;background:linear-gradient(100deg,#eef0f3 0%,#d9dde3 20%,#9fb0c6 55%,#3d67b0 80%,#2a3f6e 100%)}
.kicker{left:71px;top:244px;color:var(--red);font-size:19px;font-weight:500}
.hero h1{position:absolute;left:70px;top:178px;font-size:52px;line-height:66px;font-weight:800;color:var(--navy-dark);white-space:nowrap}
.hero p{position:absolute;left:75px;top:383px;font-size:17px;line-height:21px;color:#222}
.unit{left:457px;top:659px;width:264px;height:105px;border-radius:6px;background:linear-gradient(#ffffff,#e4e6ea);box-shadow:0 6px 14px rgba(0,0,0,.18);z-index:1}

/* split band */
.band-l{left:0;top:726px;width:599px;height:367px;background:var(--navy)}
.band-r{left:599px;top:726px;width:601px;height:367px;background:var(--red)}
.band-title{position:absolute;color:var(--white);font-weight:600;font-size:30px;line-height:37px;text-transform:uppercase}

/* about */
.about-img1{left:95px;top:1232px;width:367px;height:423px;background:linear-gradient(135deg,#c9ccd2,#8796ad 50%,#3f5a9a)}
.about-img2{left:344px;top:1456px;width:227px;height:281px;background:linear-gradient(160deg,#7d7f86,#b6a99a 50%,#4b4d53)}
.about h2{position:absolute;left:651px;top:1314px;font-size:30px;font-weight:600;color:var(--navy-dark)}
.about p{position:absolute;left:655px;width:470px;font-size:16px;line-height:19.5px;color:#555}

/* services */
.services{left:0;top:1825px;width:1200px;height:661px;background:linear-gradient(180deg,#2e3d80,#2a3676 60%,#26336f)}
.sec-title{position:absolute;width:100%;text-align:center;font-size:28px;font-weight:600;color:var(--white);text-transform:uppercase}
.card{position:absolute;width:223px;background:var(--white)}
.card .img{height:163px}
.card h3{font-size:16px;font-weight:600;color:var(--navy-dark);margin:20px 0 0 20px}
.card p{font-size:10px;line-height:12px;color:#777;margin:10px 20px 0 20px}
.card a{display:block;font-size:9px;font-weight:700;color:var(--red);margin:16px 0 0 20px;text-decoration:none}

/* products */
.prod-title{top:2590px;color:var(--navy-dark)}
.prod{position:absolute;width:210px;height:256px;border-radius:22px;background:var(--white);box-shadow:0 6px 22px rgba(0,0,0,.12);text-align:center}
.prod .img{width:110px;height:100px;margin:30px auto 0;border-radius:6px}
.prod h4{font-size:14px;font-weight:600;margin-top:12px}
.prod .price{font-size:19px;font-weight:600;color:var(--red);margin-top:6px}
.prod .price s{color:#888;font-weight:500;margin-left:4px}
.prod .buy{display:inline-block;margin-top:10px;width:110px;height:29px;line-height:29px;background:var(--red);color:var(--white);font-size:9px;font-weight:600}

/* reviews */
.reviews{left:0;top:3151px;width:1200px;height:559px;background:linear-gradient(180deg,#2b3a7f,#283574)}
.review{position:absolute;top:3302px;width:426px;height:283px;background:var(--white);border-radius:4px}
.review p{position:absolute;left:38px;top:42px;width:360px;font-size:16px;line-height:28px;font-style:italic;color:#333}
.avatar{position:absolute;left:33px;top:167px;width:90px;height:90px;border-radius:50%;border:4px solid #e69a4a;background:linear-gradient(135deg,#8a6b55,#c9a68a)}
.review .name{position:absolute;left:135px;top:188px;font-size:20px;font-weight:600}
.review .role{position:absolute;left:135px;top:218px;font-size:15px;color:var(--red)}
.dot{position:absolute;top:3640px;width:24px;height:24px;border-radius:50%;background:var(--white)}
.dot.on{background:var(--red)}

/* contact */
.ic{position:absolute;left:65px;width:76px;height:76px;border-radius:50%;background:var(--red);display:flex;align-items:center;justify-content:center}
.c-label{position:absolute;font-size:28px;font-weight:600;color:var(--red);line-height:1}
.c-val{position:absolute;font-size:30px;color:#111;line-height:1;white-space:nowrap;z-index:2}
.rule{position:absolute;width:3px;background:var(--red)}
.person{left:534px;top:3819px;width:290px;height:569px;background:linear-gradient(180deg,#f2f3f6,#3d5fb4 30%,#233f8f 80%,#b08a4a)}
.quote{left:824px;top:3875px;width:357px;height:513px;background:var(--navy)}
.quote h3{position:absolute;left:52px;top:46px;font-size:23px;font-weight:600;color:var(--white)}
.field{position:absolute;left:45px;width:267px;height:45px;background:var(--white);border:1px solid #ccc;font-size:10px;color:#888;padding:15px 18px}

/* footer */
.footer{left:0;top:4388px;width:1200px;height:380px;background:var(--footer);color:var(--white)}
.footer h5{position:absolute;font-size:22px;font-weight:500}
.footer a{position:absolute;color:var(--white);text-decoration:none;font-size:16px}
.vline{position:absolute;width:2px;background:#ddd}
.copy{left:0;top:4768px;width:1200px;height:55px;background:var(--red);color:var(--white);font-size:12px;text-align:center;line-height:55px}
</style>
</head>
<body>

<!-- header -->
<div class="abs brand"><i></i><span>Coastal Breeze Cooling Company</span></div>
<div class="abs topbar">
  <div class="item" style="left:32px">
    <svg width="13" height="10" viewBox="0 0 13 10"><rect width="13" height="10" rx="1" fill="#fff"/><path d="M0 1l6.5 5L13 1" stroke="#d8222b" stroke-width="1.3" fill="none"/></svg>
    info@cbcooling.com</div>
  <div class="item" style="left:240px">
    <svg width="12" height="12" viewBox="0 0 24 24"><path fill="#fff" d="M6.6 10.8a15 15 0 006.6 6.6l2.2-2.2c.3-.3.7-.4 1-.2 1.1.4 2.3.6 3.6.6.6 0 1 .4 1 1V20c0 .6-.4 1-1 1A17 17 0 013 4c0-.6.4-1 1-1h3.5c.6 0 1 .4 1 1 0 1.3.2 2.5.6 3.6.1.3 0 .7-.2 1z"/></svg>
    (813) 555 0190</div>
  <div class="social"><span></span><span></span><span></span></div>
</div>
<nav class="abs nav">
  <a style="left:0">HOME</a>
  <a style="left:91px">ABOUT</a>
  <a style="left:191px">SERVICES</a>
  <a style="left:313px">PRODUCTS</a>
  <a style="left:453px">CONTACT US</a>
</nav>
<div class="btn navy" style="left:993px;top:53px;width:145px;height:36px;font-size:14px">Get a Quote</div>

<!-- hero -->
<section class="abs hero">
  <div class="ph hero-photo" role="img" aria-label="HVAC technician in blue cap and overalls servicing a wall-mounted air conditioner"></div>
  <h1>HEATING &amp; AIR<br>CONDITIONING<br>SERVICES</h1>
  <p>Lorem ipsum dolor sit amet, consectetuer adipiscing elit.<br>Aenean commodo ligula eget dolor.</p>
</section>
<div class="abs kicker">BEST HVAC SERVICE PROVIDER</div>
<div class="btn" style="left:75px;top:556px;width:195px;height:49px;font-size:19px">Get a Quote</div>

<!-- split band -->
<div class="abs band-l"></div>
<div class="abs band-r"></div>
<div class="ph unit" role="img" aria-label="Wall-mounted split air conditioning unit blowing cool air"></div>
<svg class="abs" style="left:71px;top:782px" width="70" height="70" viewBox="0 0 70 70" stroke="#fff" stroke-width="5" stroke-linecap="round" fill="none">
  <path d="M35 4v62M8 19.5l54 31M8 50.5l54-31"/>
  <path d="M27 8l8 7 8-7M27 62l8-7 8 7M6 30l11 2-4 10M64 30l-11 2 4 10M6 40l11-2-4-10M64 40l-11-2 4-10"/>
</svg>
<div class="band-title" style="left:73px;top:869px">Get the best air<br>conditioning<br>services</div>
<div class="btn" style="left:75px;top:1001px;width:196px;height:49px;font-size:19px">Get a Quote</div>
<svg class="abs" style="left:1043px;top:767px" width="74" height="75" viewBox="0 0 74 75" stroke="#fff" stroke-width="4" stroke-linecap="round" fill="none">
  <path d="M14 4c-6 6 6 12 0 18s6 12 0 18M30 4c-6 6 6 12 0 18s6 12 0 18M46 4c-6 6 6 12 0 18s6 12 0 18"/>
  <path d="M4 52h66M4 64h66"/>
</svg>
<div class="band-title" style="right:69px;top:859px;text-align:right">Book a professional<br>heatingservices in<br>Tampa Bay</div>
<div class="btn navy" style="left:936px;top:986px;width:195px;height:45px;font-size:19px">Get a Quote</div>

<!-- about -->
<section class="about">
  <div class="ph about-img1" role="img" aria-label="Two technicians in hard hats inspecting a ceiling ventilation duct"></div>
  <div class="ph about-img2" role="img" aria-label="Technician working on an indoor air conditioning unit"></div>
  <h2>ABOUT US</h2>
  <p style="top:1376px">Lorem ipsum dolor sit amet, consectetuer adipiscing elit. Aenean commodo ligula eget dolor.<br>Aenean massa. Cum sociis natoque penatibus et magnis dis parturient montes, nascetur ridiculus mus.</p>
  <p style="top:1463px">Lorem ipsum dolor sit amet, consectetuer adipiscing elit. Aenean commodo ligula eget dolor.<br>Aenean massa. Cum sociis natoque penatibus et magnis dis parturient montes, nascetur ridiculus mus.</p>
</section>
<div class="btn" style="left:655px;top:1578px;width:193px;height:49px;font-size:19px">Read More</div>

<!-- services -->
<section class="abs services">
  <div class="sec-title" style="top:80px">Services We Provide</div>
  <div class="card" style="left:77px;top:189px;height:319px">
    <div class="img" role="img" aria-label="Technician installing an outdoor condenser unit" style="background:linear-gradient(135deg,#5a5e66,#c5c8cc)"></div>
    <h3>New Installs</h3>
    <p>Fast, tidy installs of new systems sized right for your home.</p>
    <a>READ MORE</a>
  </div>
  <div class="card" style="left:350px;top:189px;height:319px">
    <div class="img" role="img" aria-label="Technician in a cap maintaining an indoor unit" style="background:linear-gradient(135deg,#b9b2a8,#e9e6e1)"></div>
    <h3>Maintenance</h3>
    <p>Seasonal tune-ups that keep your cooling running at its best.</p>
    <a>READ MORE</a>
  </div>
  <div class="card" style="left:625px;top:189px;height:319px">
    <div class="img" role="img" aria-label="Technician in blue cap fitting pipework" style="background:linear-gradient(135deg,#2d2f35,#7f7466)"></div>
    <h3>Pipe Fitting</h3>
    <p>Precise copper and drain line work done by licensed local pros.</p>
    <a>READ MORE</a>
  </div>
  <div class="card" style="left:899px;top:189px;height:319px">
    <div class="img" role="img" aria-label="Gloved hands checking refrigerant lines with tools" style="background:linear-gradient(135deg,#3b6fb8,#d7dbe2)"></div>
    <h3>Leak Detection</h3>
    <p>We find and seal refrigerant leaks before they cost you more.</p>
    <a>READ MORE</a>
  </div>
</section>
<div class="btn" style="left:504px;top:2391px;width:191px;height:46px;font-size:19px">View All</div>

<!-- products -->
<div class="sec-title prod-title">Our Best Sellng Products</div>
<div class="prod" style="left:97px;top:2683px">
  <div class="img" role="img" aria-label="Blower motor wheel" style="background:linear-gradient(135deg,#d8d4cc,#8c857b)"></div>
  <h4>Product Title</h4><div class="price">$100<s>$150</s></div><span class="buy">BUY NOW</span>
</div>
<div class="prod" style="left:365px;top:2683px">
  <div class="img" role="img" aria-label="Run capacitor with wires" style="background:linear-gradient(135deg,#eee,#333 60%,#c9702d)"></div>
  <h4>Product Title</h4><div class="price">$100<s>$150</s></div><span class="buy">BUY NOW</span>
</div>
<div class="prod" style="left:631px;top:2683px">
  <div class="img" role="img" aria-label="Coiled temperature sensor cable" style="background:linear-gradient(135deg,#f4f4f4,#9a9a9a)"></div>
  <h4>Product Title</h4><div class="price">$100<s>$150</s></div><span class="buy">BUY NOW</span>
</div>
<div class="prod" style="left:899px;top:2683px">
  <div class="img" role="img" aria-label="Coiled temperature sensor cable" style="background:linear-gradient(135deg,#f4f4f4,#9a9a9a)"></div>
  <h4>Product Title</h4><div class="price">$100<s>$150</s></div><span class="buy">BUY NOW</span>
</div>
<div class="btn" style="left:515px;top:3016px;width:193px;height:47px;font-size:19px">View All</div>

<!-- reviews -->
<section class="abs reviews"><div class="sec-title" style="top:59px">Customer Reviews</div></section>
<div class="review" style="left:157px">
  <p>Lorem ipsum dolor sit amet, consectetuer adipiscing elit. Aenean commodo ligula eget dolor aenean massa.</p>
  <div class="avatar" role="img" aria-label="Customer portrait"></div>
  <div class="name">Dana R. Whitlow</div><div class="role">Manager</div>
</div>
<div class="review" style="left:638px">
  <p>Lorem ipsum dolor sit amet, consectetuer adipiscing elit. Aenean commodo ligula eget dolor aenean massa.</p>
  <div class="avatar" role="img" aria-label="Customer portrait"></div>
  <div class="name">Dana R. Whitlow</div><div class="role">Manager</div>
</div>
<div class="dot" style="left:563px"></div>
<div class="dot on" style="left:604px"></div>
<div class="dot" style="left:645px"></div>

<!-- contact -->
<div class="ph person" role="img" aria-label="Smiling HVAC technician in blue uniform and tool belt pointing to the contact details"></div>

<div class="ic" style="top:3942px">
  <svg width="38" height="38" viewBox="0 0 24 24"><path fill="#fff" d="M6.6 10.8a15 15 0 006.6 6.6l2.2-2.2c.3-.3.7-.4 1-.2 1.1.4 2.3.6 3.6.6.6 0 1 .4 1 1V20c0 .6-.4 1-1 1A17 17 0 013 4c0-.6.4-1 1-1h3.5c.6 0 1 .4 1 1 0 1.3.2 2.5.6 3.6.1.3 0 .7-.2 1z"/></svg>
</div>
<div class="rule" style="left:172px;top:3945px;height:75px"></div>
<div class="c-label" style="left:189px;top:3944px">PHONE</div>
<div class="c-val" style="left:185px;top:3986px">(813) 555 0147</div>

<div class="ic" style="top:4067px">
  <svg width="36" height="28" viewBox="0 0 36 28"><rect x="1" y="1" width="34" height="26" rx="3" fill="#fff"/><path d="M2 4l16 12L34 4" stroke="#d8222b" stroke-width="3" fill="none"/></svg>
</div>
<div class="rule" style="left:166px;top:4070px;height:75px"></div>
<div class="c-label" style="left:183px;top:4069px">EMAIL</div>
<div class="c-val" style="left:182px;top:4111px">help@cbcooling.com</div>

<div class="ic" style="top:4198px">
  <svg width="30" height="40" viewBox="0 0 30 40"><path fill="#fff" d="M15 1C7.3 1 1 7.2 1 14.9 1 25.3 15 39 15 39s14-13.7 14-24.1C29 7.2 22.7 1 15 1z"/><circle cx="15" cy="15" r="5.5" fill="#d8222b"/></svg>
</div>
<div class="rule" style="left:166px;top:4200px;height:75px"></div>
<div class="c-label" style="left:183px;top:4200px">ADDRESS</div>
<div class="c-val" style="left:180px;top:4242px">Tempa Bay, USA</div>

<section class="abs quote">
  <h3>GET A FREE QUOTE</h3>
  <div class="field" style="top:110px">Your Name</div>
  <div class="field" style="top:165px">Your Email</div>
  <div class="field" style="top:221px">Your Subject</div>
  <div class="field" style="top:275px">Your Phone Number</div>
  <div class="field" style="top:329px;height:83px">Your Message</div>
</section>
<div class="btn" style="left:869px;top:4300px;width:183px;height:43px;font-size:19px">Get a Quote</div>

<!-- footer -->
<footer class="abs footer">
  <div class="brand" style="position:absolute;left:75px;top:185px;width:245px;color:var(--white);font-size:19px"><i></i><span>Coastal Breeze Cooling Company</span></div>
  <div class="vline" style="left:361px;top:142px;height:169px"></div>
  <h5 style="left:401px;top:128px">Explore</h5>
  <a style="left:401px;top:168px">Home</a>
  <a style="left:401px;top:211px">About</a>
  <a style="left:401px;top:255px">Services</a>
  <a style="left:535px;top:170px">Products</a>
  <a style="left:535px;top:212px">Testimonials</a>
  <a style="left:538px;top:255px">Contact</a>
  <h5 style="left:724px;top:128px">Quick Links</h5>
  <a style="left:725px;top:172px">Privacy Policy</a>
  <a style="left:727px;top:209px">Terms &amp; Conditions</a>
  <a style="left:730px;top:246px">Cokkies Policy</a>
  <div class="vline" style="left:914px;top:142px;height:130px"></div>
  <h5 style="left:960px;top:128px">Newsletter</h5>
  <div class="abs" style="left:960px;top:180px;width:180px;height:37px;background:#fff;color:#888;font-size:15px;padding:8px 12px">Email Address</div>
  <div class="btn" style="left:960px;top:230px;width:180px;height:38px;font-size:17px">Signup Now</div>
</footer>
<div class="abs copy">Privacy Policy | © Copyright Coastal Breeze 2022 |</div>

</body>
</html>
```